BFCM Creatives Theme

We are looking for an initial design for our BFCM campaign this year to set the theme for all other creatives for BFCM. We are an ecommerce brand selling Merino wool baby clothing. Our flagship product is the Marlow Toddler Hush Pod (see images).

We are starting with the request for an instagram post, announcing the sale (details below). This post should be 1080x1350 but also look appealing in the square grid. I've attached a basic brand card showing color palette, fonts, and logos. I will also attach some image options. We are looking for your creativity to shine while aligning with our branding and connecting with the customer. If you have a specific idea and are looking for a specific image please contact us.

Sale Details:
- 20% Off Sitewide
- 11.28.24 - 12.02.24
- Excluding giftcards and imperfects. No rainchecks.

```html
<!DOCTYPE html>
<html lang="en">
<head>
<meta charset="utf-8">
<title>Lanora BFCM Sale Post</title>
<link rel="stylesheet" href="https://fonts.googleapis.com/css2?family=Poppins:wght@500;700;800&family=Kalam:wght@300&display=swap">
<style>
  :root {
    --stage: #5e5e60;
    --blush: #efd7de;
    --ink: #333436;
    --paper: #f1eeec;
    --sheet: #ecebea;
    --sack: #f4d2d7;
    --sack-deep: #eebcc4;
    --marker: rgba(51, 52, 54, 0.35);
  }
  * { margin: 0; padding: 0; box-sizing: border-box; }
  html, body {
    width: 1200px; height: 1197px; overflow: hidden;
    background: var(--stage);
  }
  .post-frame {
    position: absolute; left: 225px; top: 129px;
    width: 750px; height: 938px; overflow: hidden;
  }
  .post {
    position: absolute; left: 0; top: 0;
    width: 1080px; height: 1350px;
    transform: scale(0.69444); transform-origin: 0 0;
    background: var(--blush);
    font-family: "Poppins", sans-serif; color: var(--ink);
  }
  .post > * { position: absolute; }
  .info-panel { left: 0; top: 0; width: 446px; height: 1255px; background: var(--blush); }

  .hero-photo {
    left: 445px; top: 0; width: 635px; height: 1350px;
    background:
      radial-gradient(ellipse 330px 560px at 62% 72%, var(--sack-deep) 0%, var(--sack) 55%, rgba(244,210,215,0) 100%),
      radial-gradient(ellipse 200px 210px at 55% 33%, #f3dcd2 0%, rgba(243,220,210,0) 100%),
      linear-gradient(180deg, var(--sheet) 0%, #efe8e7 45%, var(--sack) 100%);
  }
  .photo-marker {
    position: absolute; inset: 70px 60px 70px 60px;
    border: 3px dashed var(--marker); border-radius: 6px;
    display: flex; align-items: center; justify-content: center;
  }
  .photo-icon { width: 120px; height: 96px; }

  .top-bar { left: 741px; top: 0; width: 339px; height: 32px; background: var(--ink); }
  .corner-square { left: 961px; top: 55px; width: 86px; height: 86px; background: var(--ink); }
  .stripe { height: 26px; background: var(--paper); }
  .stripe-left-1 { left: 0; top: 22px; width: 155px; }
  .stripe-left-2 { left: 0; top: 74px; width: 155px; }
  .stripe-right-1 { left: 927px; top: 1009px; width: 153px; }
  .stripe-right-2 { left: 927px; top: 1061px; width: 153px; }

  .headline {
    left: 40px; top: 150px; font-weight: 700;
    font-size: 196px; line-height: 176px; letter-spacing: -4px;
  }
  .headline .off { display: block; font-size: 176px; letter-spacing: 0; }
  .sitewide-band {
    left: 0; top: 504px; width: 446px; height: 111px; background: var(--paper);
    font-weight: 700; font-size: 86px; line-height: 113px; padding-left: 42px;
  }
  .calendar-icon { left: 182px; top: 670px; width: 70px; height: 72px; }
  .sale-dates {
    left: 28px; top: 750px; font-weight: 700; font-size: 46px;
    letter-spacing: -0.5px; word-spacing: 4px;
  }
  .terms {
    left: 44px; top: 832px; list-style: none;
    font-family: "Kalam", cursive; font-weight: 300; font-size: 40px; line-height: 55px;
  }
  .terms li { position: relative; padding-left: 44px; margin-bottom: 20px; }
  .terms li::before {
    content: ""; position: absolute; left: 3px; top: 25px;
    width: 14px; height: 14px; border-radius: 50%; background: var(--ink);
  }
  .brand-band {
    left: 0; top: 1048px; width: 712px; height: 90px; background: var(--paper);
    display: flex; align-items: center; justify-content: center; gap: 18px;
  }
  .brand-dot { width: 52px; height: 52px; border-radius: 50%; background: var(--ink); }
  .brand-name { font-weight: 500; font-size: 60px; line-height: 1; color: var(--ink); }
  .bottom-bar { left: 0; top: 1255px; width: 549px; height: 95px; background: var(--ink); }
</style>
</head>
<body>
  <div class="post-frame">
    <div class="post">
      <div class="info-panel"></div>
      <div class="hero-photo" role="img" aria-label="Photo placeholder: smiling baby lying on a white sheet wearing a pale pink sleep sack printed with strawberries">
        <div class="photo-marker">
          <svg class="photo-icon" viewBox="0 0 120 96" aria-hidden="true">
            <rect x="4" y="4" width="112" height="88" rx="8" fill="none" stroke="rgba(51,52,54,0.35)" stroke-width="6"/>
            <circle cx="38" cy="32" r="10" fill="rgba(51,52,54,0.35)"/>
            <path d="M12 84 L46 50 L66 68 L84 48 L108 84 Z" fill="rgba(51,52,54,0.35)"/>
          </svg>
        </div>
      </div>
      <div class="top-bar"></div>
      <div class="corner-square"></div>
      <div class="stripe stripe-left-1"></div>
      <div class="stripe stripe-left-2"></div>
      <div class="stripe stripe-right-1"></div>
      <div class="stripe stripe-right-2"></div>

      <h1 class="headline">20%<span class="off">OFF</span></h1>
      <div class="sitewide-band">Sitewide</div>

      <svg class="calendar-icon" viewBox="0 0 70 74" aria-hidden="true">
        <rect x="3" y="10" width="64" height="60" rx="6" fill="none" stroke="#333436" stroke-width="5"/>
        <rect x="3" y="10" width="64" height="14" fill="#333436"/>
        <rect x="15" y="2" width="6" height="16" rx="3" fill="#333436"/>
        <rect x="49" y="2" width="6" height="16" rx="3" fill="#333436"/>
        <g fill="#333436">
          <rect x="11" y="30" width="9" height="8"/><rect x="23" y="30" width="9" height="8"/><rect x="35" y="30" width="9" height="8"/><rect x="47" y="30" width="9" height="8"/>
          <rect x="11" y="41" width="9" height="8"/><rect x="23" y="41" width="9" height="8"/><rect x="35" y="41" width="9" height="8"/><rect x="47" y="41" width="9" height="8"/>
          <rect x="11" y="52" width="9" height="8"/><rect x="23" y="52" width="9" height="8"/><rect x="35" y="52" width="9" height="8"/><rect x="47" y="52" width="9" height="8"/>
        </g>
      </svg>
      <p class="sale-dates">11.28.24 - 12.02.24</p>

      <ul class="terms">
        <li>Excluding giftcards<br>and imperfects</li>
        <li>No rainchecks</li>
      </ul>

      <div class="brand-band">
        <span class="brand-dot"></span>
        <span class="brand-name">Lanora</span>
      </div>
      <div class="bottom-bar"></div>
    </div>
  </div>
</body>
</html>
```